Combat Sports news website design

Redesigning our existing website to make it more modern, responsive and suitable for our needs. The design needs to take in to account all aspects of our current website structure and services. View the existing website at https://www.ringpulse.co.nz

Particular attention should be paid to our livestream service, which is growing and needs to be much more user friendly to the current experience.

The homepage, article listings and article pages need designs.

Target Market(s)

Combat sports fans

Industry/Entity Type

Media

Coding

Coded - Design and coding required

Number of Pages Required

5+ page

Font styles to use
Sans Serif

Requirements
Must have
• All the functionality of the existing website must be taken in to account, and improved upon.
New design must incorporate our existing logo/colour scheme as this has only just been designed.

```html
<!DOCTYPE html>
<html lang="en">
<head>
<meta charset="utf-8">
<title>Ring Pulse – Live Event</title>
<link href="https://fonts.googleapis.com/css2?family=Bebas+Neue&family=Roboto:wght@400;500;700&display=swap" rel="stylesheet">
<style>
:root{
  --red:#a81f26;
  --red-text:#b3171f;
  --ribbon:#7d1419;
  --nav:#2b2b2b;
  --ink:#1c1c1c;
  --grey:#777;
  --light:#eeeeee;
  --footer:#333333;
  --field:#4a4a4a;
  --foot-head:#6f6f6f;
}
*{box-sizing:border-box;margin:0;padding:0}
html,body{width:1200px;height:2459px;overflow:hidden}
body{position:relative;background:#fff;font-family:"Roboto",sans-serif;color:var(--ink)}
.abs{position:absolute}
.display{font-family:"Bebas Neue",sans-serif;letter-spacing:.2px}

/* hero */
.hero{left:0;top:0;width:1200px;height:735px;background:radial-gradient(ellipse at 45% 35%,#7a5d4c 0%,#4a3a32 35%,#2a2626 70%,#1d1f24 100%)}
.hero-shade{left:0;top:0;width:1200px;height:735px;background:rgba(0,0,0,.25)}
.play{left:566px;top:361px}

.topnav{left:0;top:0;width:1200px;height:60px;background:var(--nav)}
.topnav a{position:absolute;top:18px;color:#fff;text-decoration:none;font-family:"Bebas Neue",sans-serif;font-size:19px;line-height:24px}
.topnav .big{font-size:24px;top:16px}
.nav-active{left:355px;top:57px;width:135px;height:3px;background:var(--red)}
.brand-top{left:560px;top:12px;width:80px;text-align:center;color:#fff;font-family:"Bebas Neue",sans-serif;font-size:20px;line-height:18px}
.subnav{left:0;top:60px;width:1200px;height:49px;background:rgba(30,30,34,.6)}
.subnav a{position:absolute;top:16px;color:#bbb;text-decoration:none;font-family:"Bebas Neue",sans-serif;font-size:18px}
.subnav a.on{color:#fff}

/* event info */
.event-head{left:73px;top:750px;display:flex;align-items:flex-start;gap:10px;white-space:nowrap}
.event-title{font-size:33px;line-height:40px;color:#111;font-weight:400}
.live{color:var(--red-text);font-size:19px;line-height:22px;font-family:"Bebas Neue",sans-serif}
.venue{left:73px;top:790px;font-size:17px}
.desc{left:73px;top:822px;width:565px;font-size:13.5px;line-height:14.5px;color:#333}
.viewers{left:784px;top:765px;font-size:14px;font-weight:700;color:#444}
.share{left:886px;top:762px;height:22px;border-left:1px solid #ccc}
.rule{left:73px;top:906px;width:1057px;height:1px;background:#e2e2e2}
.vrule{left:737px;top:943px;width:1px;height:1055px;background:#e6e6e6}

/* other events */
.section-head{font-size:32px;line-height:34px}
.section-head .hl{color:var(--red-text)}
.card{left:120px;width:551px;height:156px;background:var(--red);box-shadow:0 2px 4px rgba(0,0,0,.2)}
.card .poster{position:absolute;left:0;top:0;width:222px;height:156px}
.card h3{position:absolute;left:249px;top:15px;width:226px;white-space:nowrap;overflow:hidden;color:#fff;font-family:"Bebas Neue",sans-serif;font-weight:400;font-size:19px}
.card .date{position:absolute;left:249px;top:41px;color:#e6b5b7;font-size:12.5px}
.card .time{position:absolute;left:402px;top:41px;color:#e6b5b7;font-size:12.5px}
.card .place{position:absolute;left:249px;top:74px;color:#fff;font-size:14px}
.card .btn{position:absolute;top:119px;width:105px;height:26px;font-size:12.5px;font-weight:700;text-align:center;line-height:24px}
.card .sub{left:249px;background:#fff;color:var(--red-text)}
.card .more{left:394px;border:2px solid #fff;color:#fff;line-height:22px}
.card .ribbon{position:absolute;left:481px;top:0;width:56px;height:64px;background:var(--ribbon);clip-path:polygon(0 0,100% 0,100% 100%,50% 82%,0 100%);color:#fff;text-align:center;padding-top:9px;font-size:14px;line-height:18px}
.card .ribbon b{font-size:16px}
.missed{left:120px;top:1548px;font-size:13.5px;font-weight:700;color:#444;line-height:21px}
.missed span{color:var(--red-text)}

/* sidebar */
.side-head{width:300px;text-align:center;font-size:22px;color:#111}
.ad{left:783px;width:278px;height:198px;background:var(--light);color:#d7d7d7;font-family:"Bebas Neue",sans-serif;font-size:36px;line-height:42px;text-align:center;padding-top:38px}
.news{left:772px;width:300px}
.news small{display:block;font-size:7.5px;color:#444}
.news a{display:block;color:var(--red-text);text-decoration:none;font-size:14.5px;font-weight:500;line-height:17px}
.opinion-sub{left:783px;top:1853px;font-size:18px}
.opts{left:783px;width:280px;font-family:"Bebas Neue",sans-serif;font-size:29px;color:#c6c6c6;display:flex;justify-content:space-between}
.opts .pick{color:var(--red-text)}
.vote{top:1969px;height:37px;background:var(--red-text);color:#fff;text-align:center;font-family:"Bebas Neue",sans-serif;font-size:23px;line-height:39px}

/* footer */
.footer{left:0;top:2049px;width:1200px;height:410px;background:var(--footer)}
.foot-brand{left:83px;top:2072px;color:#fff;font-family:"Bebas Neue",sans-serif;font-size:52px;line-height:46px}
.foot-brand i{display:inline-block;width:14px;height:14px;background:#fff;margin-left:4px;vertical-align:middle}
.author{left:83px;top:2200px;color:#bbb;font-size:19px;font-weight:700}
.bio{left:83px;top:2224px;width:242px;color:#bbb;font-size:14px;line-height:16.6px;text-align:justify}
.foot-head{color:var(--foot-head);font-size:13.5px;font-weight:700}
.links{color:#e6e6e6;font-size:15px;line-height:20.8px;letter-spacing:.6px}
.field{left:858px;width:180px;height:22px;background:var(--field);color:#ddd;font-size:10.5px;padding:5px 10px;letter-spacing:.4px}
.submit{left:858px;top:2395px;width:78px;height:22px;background:var(--red-text);color:#fff;text-align:center;font-family:"Bebas Neue",sans-serif;font-size:19px;line-height:23px}
.copy{left:83px;top:2427px;color:#ccc;font-size:8.5px}
.help{left:453px;top:2429px;color:var(--foot-head);font-size:13px;font-weight:700}
.mail{left:577px;top:2427px;color:#ddd;font-size:15px}
</style>
</head>
<body>

<div class="abs hero" role="img" aria-label="Photo of two Muay Thai fighters clinching in a boxing ring"></div>
<div class="abs hero-shade"></div>
<svg class="abs play" width="68" height="68" viewBox="0 0 68 68" aria-label="Play stream"><circle cx="34" cy="34" r="31" fill="none" stroke="#fff" stroke-width="5"/><path d="M27 21 L48 34 L27 47 Z" fill="#fff"/></svg>

<nav class="abs topnav">
  <a style="left:136px">Home</a>
  <a class="big" style="left:244px">Categories</a>
  <a style="left:390px">Live Events</a>
  <div class="abs brand-top">Ring<br>Pulse</div>
  <a style="left:744px">Contact Us</a>
  <a style="left:853px">About Us</a>
  <a style="left:959px">Login &nbsp;/ &nbsp;Register</a>
  <svg class="abs" style="left:1095px;top:20px" width="20" height="20" viewBox="0 0 20 20"><circle cx="8" cy="8" r="6" fill="none" stroke="#fff" stroke-width="2"/><path d="M12.5 12.5 L18 18" stroke="#fff" stroke-width="2.4"/></svg>
</nav>
<div class="abs nav-active"></div>
<nav class="abs subnav">
  <a style="left:136px">Replays</a>
  <a style="left:221px">Upcoming</a>
  <a class="on" style="left:321px">My Events</a>
</nav>

<div class="abs event-head">
  <h1 class="display event-title">Crest - Muay Thai Warrior Series</h1>
  <span class="live">Live</span>
</div>
<div class="abs venue">Harbour Fight Gym, Northcote Auckland</div>
<p class="abs desc">Both men are multiple-time New Zealand champions, though the fight will not be for a title. It will be contested over five two-minute rounds and will follow a huge fight card featuring five New Zealand title fights.</p>
<div class="abs viewers">417 VIEWERS</div>
<div class="abs share"></div>
<svg class="abs" style="left:893px;top:764px" width="220" height="18" viewBox="0 0 220 18" aria-label="Share options">
  <circle cx="9" cy="9" r="7" fill="#444"/>
  <circle cx="49" cy="9" r="7" fill="#444"/>
  <circle cx="90" cy="9" r="7" fill="#444"/>
  <circle cx="132" cy="9" r="7" fill="#444"/>
  <rect x="166" y="1" width="10" height="5" fill="#444"/><rect x="162" y="6" width="18" height="7" fill="#444"/><rect x="166" y="11" width="10" height="6" fill="#444" stroke="#fff" stroke-width="1"/>
  <rect x="201" y="2" width="18" height="14" fill="#444"/><path d="M201 3 L210 10 L219 3" fill="none" stroke="#fff" stroke-width="1.5"/>
</svg>
<div class="abs rule"></div>
<div class="abs vrule"></div>

<h2 class="abs display section-head" style="left:250px;top:936px;width:260px;text-align:center;font-weight:400"><span class="hl">Other</span> Events</h2>

<article class="abs card" style="top:993px">
  <div class="poster" role="img" aria-label="Event poster with the fight card line-up" style="background:linear-gradient(135deg,#3b4048,#1f2226 60%,#4a4f56)"></div>
  <h3>Crest - Muay Thai Warrior Series</h3>
  <div class="date">1 May 2021</div><div class="time">&#9719; 17:00</div>
  <div class="place">Harbour Fight Gym, Northcote Auckland</div>
  <div class="btn sub">SUBSCRIBE</div><div class="btn more">READ MORE</div>
  <div class="ribbon"><b>20$</b><br>ONLY</div>
</article>
<article class="abs card" style="top:1171px">
  <div class="poster" role="img" aria-label="Event poster showing two headline fighters" style="background:linear-gradient(90deg,#6b6b6b,#b8902e 45%,#9a9a9a 60%,#d8d8d8)"></div>
  <h3>Blades Edge</h3>
  <div class="date">1 May 2021</div><div class="time">&#9719; 17:00</div>
  <div class="place">Harbour Fight Gym, Northcote Auckland</div>
  <div class="btn sub">SUBSCRIBE</div><div class="btn more">READ MORE</div>
  <div class="ribbon"><b>15$</b><br>ONLY</div>
</article>
<article class="abs card" style="top:1350px">
  <div class="poster" role="img" aria-label="Event poster featuring the eight-woman tournament line-up" style="background:linear-gradient(180deg,#8a1d6b,#c0307e 50%,#3a0c2c)"></div>
  <h3>Reign 4 - Queens of Muay Thai</h3>
  <div class="date">1 May 2021</div><div class="time">&#9719; 17:00</div>
  <div class="place">Harbour Fight Gym, Northcote Auckland</div>
  <div class="btn sub">SUBSCRIBE</div><div class="btn more">READ MORE</div>
  <div class="ribbon"><b>18$</b><br>ONLY</div>
</article>

<div class="abs missed">MISSED A LIVE EVENT?<br><span style="color:#222">No problem ! &nbsp;watch the </span><span>REPLAYS</span></div>

<aside>
  <h2 class="abs display side-head" style="left:773px;top:928px;font-weight:400">Advertisement</h2>
  <div class="abs ad" style="top:969px">Your<br>Ad<br>Here</div>

  <h2 class="abs display side-head" style="left:772px;top:1196px;font-weight:400">Latest Headlines</h2>
  <div class="abs news" style="top:1229px"><small>Wednesday 28 Apr, 2021</small><a>Tessa Morane looking to avenge her only loss</a></div>
  <div class="abs news" style="top:1275px"><small>Wednesday 28 Apr, 2021</small><a>Kahu Ellison steps into Crest 80kg<br>division on short notice</a></div>
  <div class="abs news" style="top:1337px"><small>Wednesday 28 Apr, 2021</small><a>Five WFL New Zealand Cup winners<br>crowned at Rise to Fight 9</a></div>
  <div class="abs news" style="top:1399px"><small>Wednesday 28 Apr, 2021</small><a>Tessa Morane looking to avenge her only loss</a></div>
  <div class="abs news" style="top:1443px"><small>Wednesday 28 Apr, 2021</small><a>Tessa Morane looking to avenge her only loss</a></div>
  <div class="abs news" style="top:1487px"><small>Wednesday 28 Apr, 2021</small><a>Kahu Ellison steps into Crest 80kg<br>division on short notice</a></div>

  <h2 class="abs display side-head" style="left:773px;top:1560px;font-weight:400">Advertisement</h2>
  <div class="abs ad" style="top:1597px">Your<br>Ad<br>Here</div>

  <h2 class="abs display side-head" style="left:782px;top:1824px;font-weight:400">Opinion Area</h2>
  <div class="abs opinion-sub">Select your prefered combat sport</div>
  <div class="abs opts" style="top:1884px"><span>MMA</span><span class="pick">Wrestling</span><span>Kickboxing</span></div>
  <div class="abs opts" style="top:1916px"><span>Boxing</span><span>Muay Thai</span><span>UFW</span><span>ALL</span></div>
  <div class="abs vote" style="left:783px;width:132px">Vote</div>
  <div class="abs vote" style="left:927px;width:132px">View Results</div>
</aside>

<footer class="abs footer"></footer>
<div class="abs foot-brand">Ring<i></i><br>Pulse</div>
<div class="abs author">Marina Keller</div>
<p class="abs bio">Marina has worked in the media industry since she was 15-years-old. She has worked in both radio and print, and is the co-founder and editor-in-chief of Ring Pulse. As well as being the Ring Pulse Editor, she focuses on writing for muti-discipline combat sports.</p>

<div class="abs foot-head" style="left:453px;top:2084px">SITE MAP</div>
<div class="abs links" style="left:453px;top:2108px">Home<br>MMA<br>Kickboxing<br>Boxing<br>Wrestling<br>UFW<br>PACIFICFC<br>Live events</div>
<div class="abs foot-head" style="left:612px;top:2084px">USEFULL LINKS</div>
<div class="abs links" style="left:612px;top:2108px">Site Terms<br>Advertisement<br>Contact us<br>Privacy</div>

<div class="abs foot-head" style="left:453px;top:2323px">GET IN TOUCH</div>
<svg class="abs" style="left:450px;top:2351px" width="180" height="22" viewBox="0 0 180 22" aria-label="Social channels">
  <circle cx="8" cy="11" r="9" fill="#aaa"/><circle cx="59" cy="11" r="9" fill="#aaa"/><circle cx="113" cy="11" r="9" fill="#aaa"/><circle cx="169" cy="11" r="9" fill="#aaa"/>
</svg>
<div class="abs help">NEED HELP?</div>
<svg class="abs" style="left:547px;top:2427px" width="23" height="17" viewBox="0 0 23 17"><rect width="23" height="17" fill="#aaa"/><path d="M0 1 L11.5 10 L23 1" fill="none" stroke="#333" stroke-width="1.6"/></svg>
<div class="abs mail">newsdesk@ringpulse.co.nz</div>
<div class="abs copy">Copyright © 2021-2022 RING PULSE All Rights Reserved</div>

<div class="abs foot-head" style="left:858px;top:2084px">CONTACT US</div>
<div class="abs field" style="top:2111px">First name</div>
<div class="abs field" style="top:2142px">Last name</div>
<div class="abs field" style="top:2173px">Email</div>
<div class="abs field" style="top:2204px">Phone / Mobile</div>
<div class="abs field" style="top:2234px;width:259px;height:152px">Message</div>
<div class="abs submit">Submit</div>

</body>
</html>
```